Satchel & Sundial needs new business card design

I need a new business card design. I'm looking for out-of-the-box design which represents the freedom of being a location independent entrepreneur.
I offer coaching, retreats and trips.
I would like to see designs with and without the photo.
Colors I use are black (#000000), green (#25A796) and brown (#D7C38C)
Website satchelandsundial.example

Target Market(s)

location independent entrepreneurs, digital nomads, people looking to swap the 9 to 5 for a lifestyle business

Industry/Entity Type

Business

Contact Information for Business Card

Dorota Falkner
Your Lifestyle Business Coach, Retreat & Trip Leader
http://satchelandsundial.example
hello@satchelandsundial.example
Live a life you don't need a holiday from

Font styles to use
Serif
Sans Serif

Requirements
Must have
• One side should contain only the logo. I would also consider having the "Live a life you don't need a holiday from" on that side too (depending on how it looks)
• Please show both sides on the designs.

```html
<!DOCTYPE html>
<html lang="en">
<head>
<meta charset="utf-8">
<title>Satchel &amp; Sundial — Business Card</title>
<link rel="stylesheet" href="https://fonts.googleapis.com/css2?family=Open+Sans:wght@400;600;700&display=swap">
<style>
  :root {
    --stage: #2a2a2a;
    --card-black: #050505;
    --card-glow: #262626;
    --teal: #25a796;
    --white: #f4f4f4;
    --rule: #6a6a6a;
  }
  * { margin: 0; padding: 0; box-sizing: border-box; }
  html, body { width: 1200px; height: 900px; overflow: hidden; }
  body {
    background: var(--stage);
    font-family: "Open Sans", Arial, sans-serif;
    color: var(--white);
    position: relative;
  }
  .card {
    position: absolute;
    top: 292px;
    width: 540px;
    height: 316px;
    border-radius: 18px;
    overflow: hidden;
    background: var(--card-black);
  }
  .card--info { left: 40px; }
  .card--logo {
    left: 620px;
    background: radial-gradient(ellipse at 50% 45%, var(--card-glow) 0%, var(--card-black) 70%);
  }
  .band {
    position: absolute;
    left: 0; right: 0;
    height: 22px;
    background: var(--teal);
  }
  .band--top { top: 0; }
  .band--bottom { bottom: 0; }
  .info {
    position: absolute;
    inset: 22px 0;
    display: flex;
    flex-direction: column;
    align-items: center;
    justify-content: center;
    text-align: center;
  }
  .info__name { color: var(--teal); font-weight: 700; font-size: 21px; }
  .info__title { font-size: 15px; margin-top: 4px; }
  .info__rule { width: 200px; height: 1px; background: var(--rule); margin: 16px 0; }
  .info__contact { font-size: 15px; line-height: 1.4; }
  .info__tagline { font-weight: 700; font-size: 19px; margin-top: 30px; }
  .tab {
    position: absolute;
    width: 24px;
    height: 40px;
    background: var(--teal);
  }
  .tab--right { right: 0; top: 34px; border-left: 3px solid var(--white); }
  .tab--left { left: 0; top: 214px; border-right: 3px solid var(--white); }
  .brand {
    position: absolute;
    inset: 0;
    display: flex;
    align-items: center;
    justify-content: center;
  }
  .brand__name {
    font-weight: 700;
    font-size: 38px;
    letter-spacing: 1px;
    color: var(--white);
  }
</style>
</head>
<body>
  <section class="card card--info" aria-label="Card back with contact details">
    <div class="band band--top"></div>
    <div class="info">
      <p class="info__name">Dorota Falkner</p>
      <p class="info__title">Your Lifestyle Business Coach Retreat &amp; Trip Leader</p>
      <div class="info__rule"></div>
      <p class="info__contact">hello@satchelandsundial.example<br>www.satchelandsundial.example</p>
      <p class="info__tagline">Live a life you don't need a holiday from</p>
    </div>
    <div class="band band--bottom"></div>
  </section>

  <section class="card card--logo" aria-label="Card front with brand name">
    <div class="tab tab--right"></div>
    <div class="tab tab--left"></div>
    <div class="brand">
      <p class="brand__name">Satchel &amp; Sundial</p>
    </div>
  </section>
</body>
</html>
```